DeskHarbor - Coworking website design

DeskHarbor is a new global coworking brand, growing fast and establishing stylish locations and communities that inspire innovation and collaboration all around the world.
The project includes a complete website design, focused on delivering the company’s values and messages, provide information to site visitors and to generate leads.

Please review the attached design brief, for more information.

Target Market(s)

Both men and women. Decision makers in:
Small & medium businesses in various fields, but mainly technology firms (Startups or established brands).
Global enterprises.
Dynamic “new generation” companies.
Press

Number of Pages Required

2 page

Requirements
Must have
• Project Scope & deliverables:
• Concept and design for :
• Home page
• Deliver the values mentioned above.
• Showcase the cities in which the company has locations in.
• Show customer testimonials.
• Provide an interface (form) for booking a tour and/or leaving contact details for more information (two alternatives)
• Coworking location page - Each location is in the coolest part of a different major city, and has its own address, set of amenities (kitchen, fast internet etc,), area information (public transportation accessibility, sites near by, bars and restaurants in walking distance) and pricing for private offices (based on number of people per office). Each location page must have an interface to book a location tour.
• Site Navigation (header & footer) - allow simple navigation between multiple city pages, location pages and homepage. Growth of up to 50 locations in 25 cities.
• The navigation should account for Navigation to additional pages (not commissioned in this project) such as:
• Locations
• Enterprise
• Special promotions
• Blog
• Contact us
• About us
• Note - the site should account for geolocation variable display, showing different content for different locations.
• Deliverables must include all editable graphic files (photoshop or similar), as follows:
• Home page - Desktop view (preferably both)
• Location page - Mobile web view (preferably both)
• Navigation - both options

```html
<!DOCTYPE html>
<html lang="en">
<head>
<meta charset="utf-8">
<title>DeskHarbor — Coworking</title>
<link href="https://fonts.googleapis.com/css2?family=Lato:wght@400;700;900&family=Open+Sans:wght@400;600;700&display=swap" rel="stylesheet">
<style>
:root{
  --blue:#2d8fd5;
  --blue-dark:#1f7ec4;
  --orange:#f07a3b;
  --ink:#1e1e1e;
  --text:#666;
  --muted:#999;
  --white:#fff;
  --line:#e3e3e3;
}
*{box-sizing:border-box;margin:0;padding:0}
html,body{width:1200px;height:3579px;overflow:hidden}
body{position:relative;background:var(--white);font-family:"Open Sans",sans-serif;color:var(--text)}
.abs{position:absolute}
.heading{font-family:"Lato",sans-serif;font-weight:900;color:var(--ink);text-transform:uppercase;letter-spacing:.5px}
.photo{position:absolute}

/* header */
.site-header{position:absolute;left:0;top:0;width:1200px;height:84px;background:var(--white);z-index:3}
.logo{position:absolute;left:100px;top:22px;font-family:"Lato",sans-serif;font-weight:900;font-size:34px;color:var(--blue);letter-spacing:.5px}
.main-nav{position:absolute;right:100px;top:32px;display:flex;gap:18px;font-weight:600;font-size:14px;color:#444;text-transform:uppercase}
.main-nav .active{color:var(--orange)}

/* hero */
.hero{position:absolute;left:0;top:84px;width:1200px;height:501px;background:linear-gradient(135deg,#6d6a66,#a8a39d 45%,#5c5a57);overflow:hidden}
.hero-title{position:absolute;left:0;width:1200px;top:128px;text-align:center;font-family:"Lato",sans-serif;font-weight:900;font-size:52px;color:var(--white);letter-spacing:1px}
.hero-text{position:absolute;left:300px;width:600px;top:212px;text-align:center;font-size:14px;line-height:24px;color:var(--white)}
.hero-btn{position:absolute;left:526px;top:294px;width:148px;height:44px;border:2px solid var(--white);border-radius:22px;color:var(--white);font-size:14px;font-weight:600;text-align:center;line-height:40px}
.hero-arrow{position:absolute;top:225px;color:var(--white);font-size:26px}
.hero-dots{position:absolute;left:565px;top:428px;display:flex;gap:8px}
.hero-dots span{width:12px;height:12px;border-radius:50%;background:var(--white)}
.hero-dots span.on{background:var(--orange)}
.hero-wave{position:absolute;left:0;top:520px;width:1200px;height:100px}

/* welcome */
.welcome-title{left:100px;top:698px;font-size:31px}
.welcome-text{left:100px;top:764px;width:460px;font-size:13.5px;line-height:26px}
.welcome-text p+p{margin-top:22px}
.btn-outline{display:inline-block;border:2px solid var(--orange);border-radius:20px;color:var(--orange);font-size:13px;font-weight:600;text-align:center}
.welcome-btn{left:100px;top:973px;width:136px;height:40px;line-height:36px}
.video-frame{left:627px;top:706px;width:475px;height:308px;border:1px solid var(--line);padding:6px;background:var(--white);box-shadow:0 1px 6px rgba(0,0,0,.12)}
.video-frame .photo{left:6px;top:6px;right:6px;bottom:6px;background:linear-gradient(135deg,#e9e2d6,#8a9aa6 55%,#3e4a56)}
.play{position:absolute;left:208px;top:120px;width:58px;height:58px;border-radius:50%;background:#e0262d}

/* values */
.values{position:absolute;left:0;top:1102px;width:1200px;height:478px;background:linear-gradient(180deg,#e9ecee,#f6f7f8 60%,#e4e7e9)}
.values-title{position:absolute;left:0;width:1200px;top:75px;text-align:center;font-size:33px}
.value{position:absolute;top:170px;width:240px;text-align:center}
.value-icon{width:136px;height:136px;border-radius:50%;border:3px solid var(--blue);margin:0 auto;background:rgba(255,255,255,.6)}
.value-label{margin-top:30px;font-family:"Lato",sans-serif;font-weight:700;font-size:21px;line-height:32px;color:#333}
.slider-arrow{position:absolute;top:252px;font-size:34px;color:#333}

/* news */
.news-title{left:0;width:1200px;top:1656px;text-align:center;font-size:32px}
.news-card{position:absolute;top:1758px;width:310px}
.news-card .photo{position:relative;width:310px;height:210px}
.news-card h3{margin-top:32px;font-family:"Lato",sans-serif;font-weight:700;font-size:20px;color:#222}
.news-meta{margin-top:10px;font-size:12.5px;color:#555;display:flex;align-items:center;gap:8px}
.news-meta .ico{width:11px;height:11px;background:var(--blue);border-radius:2px}
.news-card p{margin-top:14px;font-size:12.5px;line-height:23px}
.news-btn{margin-top:18px;width:126px;height:34px;line-height:30px}

/* testimonials */
.testimonials{position:absolute;left:0;top:2279px;width:1200px;height:405px;background:linear-gradient(180deg,rgba(240,122,59,.92),rgba(228,120,64,.88)),linear-gradient(90deg,#c0622e,#e0824c)}
.t-title{position:absolute;left:0;width:1200px;top:80px;text-align:center;font-family:"Lato",sans-serif;font-weight:900;font-size:32px;color:var(--white);text-transform:uppercase}
.testimonial{position:absolute;top:165px;width:330px}
.avatar{position:absolute;left:0;top:0;width:70px;height:70px;border-radius:50%;border:3px solid var(--white);background:linear-gradient(160deg,#c9b8a8,#5a4a40)}
.avatar-badge{position:absolute;left:27px;top:60px;width:18px;height:18px;border-radius:50%;background:var(--blue)}
.t-quote{position:absolute;left:84px;top:0;width:236px;font-style:italic;font-size:12px;line-height:22px;color:var(--white)}
.t-name{position:absolute;left:84px;top:112px;font-family:"Lato",sans-serif;font-weight:700;font-size:13.5px;color:#3a2416;text-transform:uppercase}
.t-role{position:absolute;left:84px;top:138px;font-size:12px;color:var(--white)}
.t-arrow{position:absolute;top:185px;width:30px;height:30px;border-radius:50%;background:#6d4a36;color:var(--white);font-size:15px;text-align:center;line-height:30px}

/* locations map */
.map{position:absolute;left:0;top:2684px;width:1200px;height:470px;background:linear-gradient(180deg,#f3f3f3,#e2e2e2)}
.pin{position:absolute;width:40px;height:54px}
.loc-box{position:absolute;left:403px;top:158px;width:394px;height:131px;background:var(--blue);color:var(--white);text-align:center}
.loc-box h2{margin-top:30px;font-family:"Lato",sans-serif;font-weight:900;font-size:24px;letter-spacing:.5px;text-transform:uppercase}
.loc-box p{margin-top:6px;font-size:16px}

/* footer */
.site-footer{position:absolute;left:0;top:3100px;width:1200px;height:479px}
.footer-wave{position:absolute;left:0;top:0;width:1200px;height:80px}
.footer-body{position:absolute;left:0;top:40px;width:1200px;height:439px;background:var(--blue-dark)}
.f-head{position:absolute;top:3197px;font-family:"Lato",sans-serif;font-weight:700;font-size:16px;color:var(--white);text-transform:uppercase}
.f-links{position:absolute;left:100px;top:3235px;list-style:none;font-size:12.5px;color:var(--white)}
.f-links li{height:28.5px}
.f-links li::before{content:"";display:inline-block;border-left:5px solid var(--white);border-top:4px solid transparent;border-bottom:4px solid transparent;margin-right:10px}
.f-contact{position:absolute;font-size:12.5px;line-height:20px;color:var(--white)}
.f-ico{position:absolute;left:403px;width:14px;height:14px}
.field{position:absolute;background:var(--white);font-size:12px;color:#777;padding:0 12px;line-height:40px}
.submit{position:absolute;left:773px;top:3381px;width:98px;height:36px;border-radius:18px;background:var(--orange);color:var(--white);font-size:13px;font-weight:700;text-align:center;line-height:36px}
.f-rule{position:absolute;top:3473px;height:1px;background:rgba(255,255,255,.5)}
.social{position:absolute;top:3455px;width:36px;height:36px;border-radius:50%;border:2px solid var(--white)}
.copyright{position:absolute;left:0;width:1200px;top:3522px;text-align:center;font-size:13px;color:var(--white)}
</style>
</head>
<body>

<header class="site-header">
  <div class="logo">DESKHARBOR</div>
  <nav class="main-nav">
    <span class="active">Home</span><span>About Us</span><span>Locations</span><span>Enterprise</span><span>Special Promotions</span><span>Blog</span><span>Contact Us</span>
  </nav>
</header>

<section class="hero" role="img" aria-label="Photo of colleagues working at laptops in a bright coworking office">
  <h1 class="hero-title">DESKHARBOR</h1>
  <p class="hero-text">DeskHarbor is a new global coworking brand, growing fast and establishing stylish locations and communities that inspire innovation and collaboration all around the world.</p>
  <div class="hero-btn">CONTACT US</div>
  <div class="hero-arrow" style="left:34px">&#8249;</div>
  <div class="hero-arrow" style="right:34px">&#8250;</div>
  <div class="hero-dots"><span class="on"></span><span></span><span></span><span></span></div>
</section>
<svg class="hero-wave" viewBox="0 0 1200 100" preserveAspectRatio="none">
  <path d="M0 0 Q300 55 600 90 Q900 55 1200 0 L1200 100 L0 100 Z" fill="#fff"/>
  <path d="M0 30 Q300 55 600 80 Q900 55 1200 30 L1200 44 Q900 70 600 96 Q300 70 0 44 Z" fill="var(--blue)"/>
  <path d="M590 47 L600 55 L610 47 M590 56 L600 64 L610 56" stroke="#666" stroke-width="2.5" fill="none"/>
</svg>

<h2 class="abs heading welcome-title">Welcome to DeskHarbor</h2>
<div class="abs welcome-text">
  <p>At vero eos et accusamus et iusto odio dignissimos ducimus qui blanditii ispr aesentium voluptatum deleniti atque corr.</p>
  <p>Rupti quos dolores et quas molestias excepturi sint occaecati cupiditate non provident, similique sunt in culpa qui officia deserunt mollitia animi, id est laborum et dolorum um quidem. Nam libero tempore, cum soluta nobis est eligendi optio cumque nihil impedit quo minus.</p>
</div>
<div class="abs btn-outline welcome-btn">READ MORE &#10140;</div>
<div class="abs video-frame">
  <div class="photo" role="img" aria-label="Video still of a team gathered around a table with laptops">
    <div class="play"><svg width="58" height="58"><path d="M23 17 L42 29 L23 41 Z" fill="#fff"/></svg></div>
  </div>
</div>

<section class="values" aria-label="Our values">
  <h2 class="heading values-title">Our Values</h2>
  <div class="slider-arrow" style="left:28px">&#8249;</div>
  <div class="slider-arrow" style="right:28px">&#8250;</div>
  <div class="value" style="left:76px">
    <div class="value-icon"><svg width="130" height="130"><circle cx="65" cy="60" r="18" fill="var(--orange)"/><rect x="57" y="80" width="16" height="12" rx="2" fill="var(--orange)"/><path d="M65 28v-8M40 38l-6-6M90 38l6-6M33 60h-8M97 60h8" stroke="var(--orange)" stroke-width="3"/></svg></div>
    <div class="value-label">Inspire Collaboration<br>and Innovation</div>
  </div>
  <div class="value" style="left:369px">
    <div class="value-icon"><svg width="130" height="130"><circle cx="65" cy="48" r="11" fill="var(--orange)"/><circle cx="44" cy="58" r="9" fill="var(--orange)"/><circle cx="86" cy="58" r="9" fill="var(--orange)"/><path d="M48 92a17 17 0 0 1 34 0Z M28 92a16 14 0 0 1 28 -6v6Z M102 92a16 14 0 0 0 -28 -6v6Z" fill="var(--orange)"/></svg></div>
    <div class="value-label">Be a Part of Sharing an<br>Exclusive Club</div>
  </div>
  <div class="value" style="left:646px">
    <div class="value-icon"><svg width="130" height="130"><rect x="40" y="60" width="12" height="32" fill="var(--orange)"/><path d="M56 62 L68 36 Q74 34 74 42 L72 56 L92 56 Q98 58 96 64 L90 90 L56 92 Z" fill="var(--orange)"/></svg></div>
    <div class="value-label">Realize Your Idea<br>Greatness</div>
  </div>
  <div class="value" style="left:904px">
    <div class="value-icon"><svg width="130" height="130"><rect x="32" y="38" width="66" height="44" rx="3" fill="none" stroke="var(--orange)" stroke-width="5"/><path d="M58 82v12h14V82M48 96h34" stroke="var(--orange)" stroke-width="5"/><path d="M50 72 L84 48" stroke="var(--orange)" stroke-width="4"/></svg></div>
    <div class="value-label">Style and Design<br>Awareness</div>
  </div>
</section>

<h2 class="abs heading news-title">Latest News</h2>
<article class="news-card" style="left:100px">
  <div class="photo" role="img" aria-label="Photo of a woman working on a laptop in a lounge" style="background:linear-gradient(135deg,#6a4a2e,#b98a52 50%,#3c3c3c)"></div>
  <h3>Foresee The Pain And Trouble</h3>
  <div class="news-meta"><span class="ico"></span>02/12/2017 &nbsp;|&nbsp; <span class="ico" style="border-radius:50%"></span>Tom Avery</div>
  <p>Nam libero tempore, cum soluta nobis est eligendi optio cumque nihil impedit quo minus id quod ma ixime placeat facere possimus</p>
  <div class="btn-outline news-btn">Read More &#10140;</div>
</article>
<article class="news-card" style="left:444px">
  <div class="photo" role="img" aria-label="Photo of an empty open-plan office with skylights" style="background:linear-gradient(180deg,#cfcfcf,#efece6 55%,#c98a4a)"></div>
  <h3>Foresee The Pain And Trouble</h3>
  <div class="news-meta"><span class="ico"></span>02/12/2017 &nbsp;|&nbsp; <span class="ico" style="border-radius:50%"></span>Tom Avery</div>
  <p>Nam libero tempore, cum soluta nobis est eligendi optio cumque nihil impedit quo minus id quod ma ixime placeat facere possimus</p>
  <div class="btn-outline news-btn">Read More &#10140;</div>
</article>
<article class="news-card" style="left:790px">
  <div class="photo" role="img" aria-label="Photo of colleagues reviewing documents together" style="background:linear-gradient(135deg,#8a8d96,#c7b9ad 50%,#4d4f5a)"></div>
  <h3>Foresee The Pain And Trouble</h3>
  <div class="news-meta"><span class="ico"></span>02/12/2017 &nbsp;|&nbsp; <span class="ico" style="border-radius:50%"></span>Tom Avery</div>
  <p>Nam libero tempore, cum soluta nobis est eligendi optio cumque nihil impedit quo minus id quod ma ixime placeat facere possimus</p>
  <div class="btn-outline news-btn">Read More &#10140;</div>
</article>

<section class="testimonials" role="img" aria-label="Orange-tinted photo of a team meeting behind client testimonials">
  <h2 class="t-title">What Our Clients Say</h2>
  <div class="t-arrow" style="left:14px">&#8249;</div>
  <div class="t-arrow" style="right:14px">&#8250;</div>
  <div class="testimonial" style="left:96px">
    <div class="avatar" role="img" aria-label="Client portrait"></div><div class="avatar-badge"></div>
    <p class="t-quote">At vero eos et accusamus et iustodio dignissimos ducimus qui blanditiipraesent ium voluptatum deleniti atque corrupti quos dolores quas molestias</p>
    <div class="t-name">Priya Dalton</div><div class="t-role">Creative Manager, USA</div>
  </div>
  <div class="testimonial" style="left:445px">
    <div class="avatar" role="img" aria-label="Client portrait"></div><div class="avatar-badge"></div>
    <p class="t-quote">At vero eos et accusamus et iustodio dignissimos ducimus qui blanditiipraesent ium voluptatum deleniti atque corrupti quos dolores quas molestias</p>
    <div class="t-name">Leo Marsh</div><div class="t-role">Creative Manager, USA</div>
  </div>
  <div class="testimonial" style="left:793px">
    <div class="avatar" role="img" aria-label="Client portrait"></div><div class="avatar-badge"></div>
    <p class="t-quote">At vero eos et accusamus et iustodio dignissimos ducimus qui blanditiipraesent ium voluptatum deleniti atque corrupti quos dolores quas molestias</p>
    <div class="t-name">Sam Keller</div><div class="t-role">Creative Manager, USA</div>
  </div>
</section>

<section class="map" role="img" aria-label="Grey world map marking DeskHarbor office cities">
  <svg width="0" height="0" style="position:absolute"><defs><symbol id="pin" viewBox="0 0 40 54"><path d="M20 2a18 18 0 0 1 18 18c0 14-18 32-18 32S2 34 2 20A18 18 0 0 1 20 2Z" fill="#d9442e"/><circle cx="20" cy="20" r="7" fill="#fff"/></symbol></defs></svg>
  <svg class="pin" style="left:78px;top:80px"><use href="#pin"/></svg>
  <svg class="pin" style="left:126px;top:140px"><use href="#pin"/></svg>
  <svg class="pin" style="left:520px;top:6px"><use href="#pin"/></svg>
  <svg class="pin" style="left:312px;top:320px"><use href="#pin"/></svg>
  <svg class="pin" style="left:830px;top:160px"><use href="#pin"/></svg>
  <svg class="pin" style="left:914px;top:112px"><use href="#pin"/></svg>
  <svg class="pin" style="left:1050px;top:84px"><use href="#pin"/></svg>
  <svg class="pin" style="left:990px;top:370px"><use href="#pin"/></svg>
  <div class="loc-box"><h2>DeskHarbor Locations</h2><p>200 Office Locations 50 Cities</p></div>
</section>

<footer class="site-footer">
  <svg class="footer-wave" viewBox="0 0 1200 80" preserveAspectRatio="none">
    <path d="M0 0 Q600 90 1200 0 L1200 80 L0 80 Z" fill="var(--orange)"/>
  </svg>
  <div class="footer-body"></div>
</footer>
<svg class="abs" style="left:0;top:3112px" width="1200" height="60" viewBox="0 0 1200 60" preserveAspectRatio="none"><path d="M0 0 Q600 96 1200 0 L1200 60 L0 60 Z" fill="var(--blue-dark)"/></svg>

<div class="f-head" style="left:100px">Quick Links</div>
<ul class="f-links"><li>Home</li><li>Locations</li><li>Enterprise</li><li>Special promotions</li><li>Blog</li><li>About Us</li><li>Contact</li></ul>

<div class="f-head" style="left:403px">Contact Us</div>
<svg class="f-ico" style="top:3254px" viewBox="0 0 14 14"><path d="M7 1a4.5 4.5 0 0 1 4.5 4.5C11.5 9 7 13 7 13S2.5 9 2.5 5.5A4.5 4.5 0 0 1 7 1Z" fill="none" stroke="#fff" stroke-width="1.3"/><circle cx="7" cy="5.5" r="1.5" fill="#fff"/></svg>
<div class="f-contact" style="left:432px;top:3248px">DESKHARBOR PVT LTD<br>48 Harbor Lane, Eastport City,<br>New State, 5678</div>
<svg class="f-ico" style="top:3336px" viewBox="0 0 14 14"><path d="M3 1l3 3-1.5 2a8 8 0 0 0 3.5 3.5L10 8l3 3-2 2C6 13 1 8 1 3Z" fill="#fff"/></svg>
<div class="f-contact" style="left:432px;top:3332px;font-weight:600">(+1) 555 010 2040</div>
<svg class="f-ico" style="top:3377px" viewBox="0 0 14 14"><rect x="1" y="3" width="12" height="9" fill="none" stroke="#fff" stroke-width="1.3"/><path d="M1 3l6 5 6-5" fill="none" stroke="#fff" stroke-width="1.3"/></svg>
<div class="f-contact" style="left:432px;top:3373px;font-weight:600">hello@deskharbor.com</div>

<div class="f-head" style="left:773px">Quick Contact</div>
<form class="quick-contact" aria-label="Quick contact and tour request">
  <div class="field" style="left:773px;top:3248px;width:157px;height:40px">Name</div>
  <div class="field" style="left:945px;top:3248px;width:155px;height:40px">Email</div>
  <div class="field" style="left:773px;top:3300px;width:327px;height:69px;line-height:28px">Message</div>
  <div class="submit">SUBMIT</div>
</form>

<div class="f-rule" style="left:100px;width:395px"></div>
<div class="f-rule" style="left:705px;width:395px"></div>
<div class="social" style="left:512px" aria-label="Social link"></div>
<div class="social" style="left:557px" aria-label="Social link"></div>
<div class="social" style="left:602px" aria-label="Social link"></div>
<div class="social" style="left:648px" aria-label="Social link"></div>
<div class="copyright">Copyrights &copy; 2017 DeskHarbor. All Rights Reserved.</div>

</body>
</html>
```